Parcelwise HQ letterhead and envelope

Design a formal (8.5x11) letterhead and envelope for sales outreach and legal matters. Using design input from https://www.parcelwisehq.example/ and the attached documents.

Industry/Entity Type

Software Service

Requirements
Must have
• These 4 hex colors are our official colors:
• #355c98 [blue]
• #1eb1a2 [teal]
• #fdba12 [gold]
• #f1653b [orange]
• So no other colors besides these should be used.

```html
<!DOCTYPE html>
<html lang="en">
<head>
<meta charset="utf-8">
<title>Parcelwise HQ – Letterhead and Envelopes</title>
<link href="https://fonts.googleapis.com/css2?family=Lato:wght@300;400;700&family=Arimo:wght@400&family=Kaushan+Script&display=swap" rel="stylesheet">
<style>
  :root{
    --blue:#355c98;
    --teal:#1eb1a2;
    --gold:#fdba12;
    --orange:#f1653b;
    --backdrop:#d6d6d6;
    --paper:#ffffff;
    --ink:#4a4a4a;
    --rule:#9a9a9a;
    --faint:#eef1f6;
  }
  *{box-sizing:border-box;margin:0;padding:0}
  html,body{width:1200px;height:753px;overflow:hidden}
  body{background:var(--backdrop);position:relative;font-family:"Lato",sans-serif}

  .sheet{position:absolute;background:var(--paper)}
  .letterhead{left:57px;top:54px;width:450px;height:636px;box-shadow:0 0 0 1px #c8c8c8}

  .brand{position:absolute;display:flex;align-items:center;gap:8px;color:var(--blue);
    font-family:"Lato",sans-serif;font-weight:300;white-space:nowrap}
  .brand-dot{border:2.4px solid var(--blue);border-radius:50%;flex:none}
  .letterhead .brand{left:24px;top:20px;font-size:22px}
  .letterhead .brand-dot{width:30px;height:30px}

  .header-address{position:absolute;right:25px;top:23px;padding-left:14px;border-left:1px solid var(--rule);
    font-family:"Arimo",sans-serif;font-size:7.5px;line-height:9.5px;color:#333}
  .header-address svg{vertical-align:-1px;margin-right:2px}

  .letter-body{position:absolute;left:33px;right:33px;top:164px;color:var(--ink);font-size:8.9px;line-height:13.6px}
  .salutation{color:var(--blue);font-weight:700;font-size:9px;margin-bottom:10px}
  .letter-body p.copy{text-align:justify;margin-bottom:10.5px}
  .closing{font-size:11px;color:#222;margin-top:10px}
  .signature{font-family:"Kaushan Script",cursive;color:var(--blue);font-size:17px;margin-top:2px}

  .faint-mark{position:absolute;left:26px;top:482px;width:122px;height:122px;border:8px solid var(--faint);border-radius:50%}

  .wave{position:absolute;left:0;bottom:0;display:block}
  .footer-contact{position:absolute;right:12px;color:var(--paper);font-family:"Arimo",sans-serif;
    font-size:7.6px;line-height:13px;text-align:right}
  .footer-contact svg{vertical-align:-1px;margin:0 2px 0 5px}
  .letterhead .footer-contact{bottom:6px}

  .envelope{width:518px;height:232px}
  .envelope-back{left:650px;top:159px;width:517px;border:1.5px solid #222}
  .envelope-middle{left:612px;top:258px;border:1.5px solid #222}
  .envelope-front{left:526px;top:361px;border:1.5px solid #222;overflow:hidden}
  .flap{position:absolute;left:0;top:0}
  .flap-mark{position:absolute;width:44px;height:44px;border-radius:50%}
  .envelope-back .flap-mark{left:322px;top:22px;border:3px solid var(--paper);transform:translateX(-50%)}
  .envelope-middle .flap-mark{left:346px;top:66px;border:3px solid var(--blue);transform:translateX(-300%)}
  .envelope-middle .flap-mark{left:258px;top:24px;transform:translateX(-50%)}
  .envelope-back .flap-mark{left:258px}

  .icon-scatter{position:absolute;left:0;top:0;width:100%;height:190px;
    background:radial-gradient(circle at 80% 35%,rgba(253,186,18,.10),transparent 30%),
               radial-gradient(circle at 18% 45%,rgba(241,101,59,.07),transparent 28%),
               radial-gradient(circle at 60% 70%,rgba(30,177,162,.06),transparent 30%)}
  .envelope-front .brand{left:18px;top:14px;font-size:20px}
  .envelope-front .brand-dot{width:28px;height:28px}
  .envelope-front .footer-contact{bottom:5px;font-size:7.8px}
</style>
</head>
<body>

<section class="sheet letterhead" aria-label="Letterhead">
  <div class="brand"><span class="brand-dot"></span>Parcelwise HQ</div>
  <address class="header-address">
    <svg width="7" height="7" viewBox="0 0 10 10"><circle cx="5" cy="5" r="4.2" fill="none" stroke="#355c98" stroke-width="1.2"/><circle cx="5" cy="4.3" r="1.4" fill="#355c98"/></svg>27 Harbor Lane<br>&nbsp;&nbsp;&nbsp;Fairview, OH 45000
  </address>

  <div class="letter-body">
    <p class="salutation">Dear Mr. Lorem,</p>
    <p class="copy">Lorem ipsum dolor sit amet, consectetuer adipiscing elit, sed diam nonummy nibh euismod tincidunt ut laoreet dolore magna aliquam erat volutpat. Ut wisi enim ad minim veniam, quis nostrud exerci tation ullamcorper suscipit lobortis nisl ut aliquip ex ea commodo consequat. Duis autem vel eum iriure dolor in hendiusto odio dignissim qui blandit praesent luptatum zzril delenit augue duis dolore te feugait nulla facilisi.</p>
    <p class="copy">Lorem ipsum dolor sit amet, consectetuer adipiscing elit, sed diam nonummy nibh euismod tincidunt ut laoreet dolore magna aliquam erat volutpat. Ut wisi enim ad minim veniam, quis nostrud exerci tation ullamcorper suscipit lobortis nisl ut aliquip ex ea commodo consequat. Duis autem vel eum iriure dolor in hendiusto odio dignissim qui blandit praesent luptatum zzril delenit augue duis dolore te feugait nulla facilisi.</p>
    <p class="copy">Lorem ipsum dolor sit amet, consectetuer adipiscing elit, sed diam nonummy nibh euismod tincidunt ut laoreet dolore magna aliquam erat volutpat. Ut wisi enim ad minim veniam, quis nostrud exerci tation ullamcorper suscipit lobortis nisl ut aliquip ex ea commodo consequat. Duis autem vel eum iriure dolor in hendiusto odio dignissim qui blandit praesent luptatum zzril delenit augue duis dolore te feugait nulla facilisi.</p>
    <p class="closing">Sincerely Your,</p>
    <p class="signature">Your Name</p>
  </div>

  <div class="faint-mark"></div>

  <svg class="wave" width="450" height="70" viewBox="0 0 450 70">
    <path d="M0,2 C40,40 110,62 200,54 C290,46 370,14 450,10 L450,70 L0,70 Z" fill="var(--blue)"/>
    <path d="M0,9 C40,44 110,60 200,50 C290,40 370,12 450,6" fill="none" stroke="var(--paper)" stroke-width="2.5"/>
    <path d="M40,30 C90,52 150,54 210,47 C290,38 360,16 430,10" fill="none" stroke="var(--teal)" stroke-width="3"/>
    <path d="M0,0 C40,34 110,55 200,46" fill="none" stroke="var(--blue)" stroke-width="1.5"/>
  </svg>
  <div class="footer-contact">
    <svg width="7" height="7" viewBox="0 0 10 10"><circle cx="5" cy="5" r="4.2" fill="none" stroke="#fff"/><rect x="3.3" y="2.5" width="3.4" height="5" rx=".6" fill="#fff"/></svg>(555) 214-0198
    <svg width="7" height="7" viewBox="0 0 10 10"><circle cx="5" cy="5" r="4.2" fill="none" stroke="#fff"/><path d="M3,3 L4.4,3 L5,4.4 L4.3,5 Q5,6.3 6,6.7 L6.6,6 L8,6.6 L8,7.6 Q5,8 2.8,4.6 Z" fill="#fff"/></svg>(555) 630-4471(Main)<br>
    <svg width="7" height="7" viewBox="0 0 10 10"><circle cx="5" cy="5" r="4.2" fill="none" stroke="#fff"/><rect x="2.6" y="3.3" width="4.8" height="3.4" fill="none" stroke="#fff" stroke-width=".8"/></svg>jdoe@parcelwisehq.example
    <svg width="7" height="7" viewBox="0 0 10 10"><circle cx="5" cy="5" r="4.2" fill="none" stroke="#fff"/><ellipse cx="5" cy="5" rx="1.8" ry="4.2" fill="none" stroke="#fff" stroke-width=".7"/><line x1=".8" y1="5" x2="9.2" y2="5" stroke="#fff" stroke-width=".7"/></svg>www.parcelwisehq.example
  </div>
</section>

<section class="sheet envelope envelope-back" aria-label="Envelope back with teal flap">
  <svg class="flap" width="514" height="95" viewBox="0 0 514 95">
    <path d="M2,0 L512,0 L504,36 C498,50 488,54 470,58 L290,90 C270,94 244,94 224,90 L48,58 C30,54 18,50 12,36 Z" fill="var(--teal)"/>
  </svg>
  <span class="flap-mark"></span>
</section>

<section class="sheet envelope envelope-middle" aria-label="Envelope back with white flap">
  <svg class="flap" width="515" height="95" viewBox="0 0 515 95">
    <path d="M2,0 L10,30 C14,44 24,50 42,54 L230,90 C248,93 268,93 286,90 L470,54 C488,50 500,44 504,30 L512,0" fill="none" stroke="#222" stroke-width="1"/>
  </svg>
  <span class="flap-mark"></span>
</section>

<section class="sheet envelope envelope-front" aria-label="Envelope front">
  <div class="icon-scatter" role="img" aria-label="Faint scattered line icons in gold, orange and teal"></div>
  <div class="brand"><span class="brand-dot"></span>Parcelwise HQ</div>
  <svg class="wave" width="518" height="65" viewBox="0 0 518 65">
    <path d="M0,6 C40,38 120,52 220,47 C330,40 420,10 518,8 L518,65 L0,65 Z" fill="var(--blue)"/>
    <path d="M0,12 C40,42 120,54 220,46 C330,37 420,8 518,3" fill="none" stroke="var(--paper)" stroke-width="2.5"/>
    <path d="M40,28 C110,48 170,48 240,42 C330,34 420,10 500,6" fill="none" stroke="var(--teal)" stroke-width="3"/>
    <path d="M0,0 C40,32 120,48 220,42" fill="none" stroke="var(--blue)" stroke-width="1.5"/>
  </svg>
  <div class="footer-contact">
    <svg width="7" height="7" viewBox="0 0 10 10"><circle cx="5" cy="5" r="4.2" fill="none" stroke="#fff"/><circle cx="5" cy="4.3" r="1.4" fill="#fff"/></svg>27 Harbor Lane, Fairview, OH 45000<br>
    <svg width="7" height="7" viewBox="0 0 10 10"><circle cx="5" cy="5" r="4.2" fill="none" stroke="#fff"/><ellipse cx="5" cy="5" rx="1.8" ry="4.2" fill="none" stroke="#fff" stroke-width=".7"/><line x1=".8" y1="5" x2="9.2" y2="5" stroke="#fff" stroke-width=".7"/></svg>www.parcelwisehq.example
  </div>
</section>

</body>
</html>
```